Law Offices business card

Hi there, I'll need business card for the Law Offices of Colin Matheny. The information must convey his strategic approach and quick resolution to complex business litigation needs. Please emphasize Civil Litigation, Corporate Law, Business Governance and Real Estate Law. Colin has over 25 years of experience in these fields.The card should be modern and edgy and the message should be clear. Please consult his current website for ideas.

```html
<!DOCTYPE html>
<html lang="en">
<head>
<meta charset="utf-8">
<title>Law Offices of Colin Matheny – Business Card</title>
<link href="https://fonts.googleapis.com/css2?family=Cinzel:wght@400&family=PT+Sans:wght@400;700&display=swap" rel="stylesheet">
<style>
  :root {
    --backdrop: #161616;
    --card-white: #ffffff;
    --brand-orange: #e97826;
    --orange-deep: #d96a1c;
    --ink: #1a1a1a;
    --text-grey: #2b2b2b;
  }
  * { margin: 0; padding: 0; box-sizing: border-box; }
  html, body {
    width: 1200px; height: 900px; overflow: hidden;
    background: var(--backdrop);
  }
  .stage { position: relative; width: 1200px; height: 900px; }
  .card {
    position: absolute; top: 170px; width: 347px; height: 561px;
    font-family: "PT Sans", Arial, sans-serif; text-align: center;
  }
  .card--front { left: 259px; background: var(--card-white); }
  .card--back { left: 631px; background: var(--brand-orange); }

  .accent-bar {
    position: absolute; left: 102px; width: 143px; height: 30px;
    background: var(--brand-orange);
  }
  .accent-bar--top { top: 0; }
  .accent-bar--bottom { bottom: 0; height: 28px; }

  .brand-mark {
    position: absolute; top: 80px; left: 123px;
    width: 100px; height: 100px; border-radius: 50%;
    background: var(--ink);
  }
  .brand-name {
    position: absolute; top: 190px; left: 0; width: 100%;
    font-family: "Cinzel", "Times New Roman", serif;
    font-weight: 400; line-height: 30px;
  }
  .brand-name__line1 {
    display: block; font-size: 27px; letter-spacing: 1px; color: var(--brand-orange);
  }
  .brand-name__line2 {
    display: block; font-size: 19px; color: var(--ink); line-height: 24px;
  }

  .person { position: absolute; top: 278px; left: 0; width: 100%; }
  .person__name {
    font-size: 21px; font-weight: 700; color: var(--brand-orange); line-height: 26px;
  }
  .person__title { font-size: 15px; color: var(--text-grey); line-height: 20px; }

  .address {
    position: absolute; top: 333px; left: 0; width: 100%;
    font-size: 15.5px; color: var(--text-grey); line-height: 21px; font-style: normal;
  }
  .contacts {
    position: absolute; top: 385px; left: 0; width: 100%;
    list-style: none; font-size: 15.5px; color: var(--text-grey); line-height: 23.5px;
  }
  .contacts li { display: flex; justify-content: center; align-items: center; gap: 6px; }
  .contacts svg { width: 11px; height: 11px; fill: var(--brand-orange); }

  .back-mark {
    position: absolute; top: 85px; left: 68px; width: 210px; height: 210px;
    border-radius: 50%; background: var(--orange-deep);
    display: flex; align-items: center; justify-content: center;
    font-family: "Cinzel", "Times New Roman", serif; font-size: 20px;
    color: var(--brand-orange); line-height: 28px; padding: 30px;
  }
  .practice-areas {
    position: absolute; top: 370px; left: 0; width: 100%;
    list-style: none; font-size: 18px; font-weight: 700; color: var(--ink);
    line-height: 25px;
  }
</style>
</head>
<body>
<main class="stage">
  <section class="card card--front" aria-label="Business card front">
    <div class="accent-bar accent-bar--top"></div>
    <div class="brand-mark"></div>
    <h1 class="brand-name">
      <span class="brand-name__line1">Law Offices</span>
      <span class="brand-name__line2">of Colin Matheny</span>
    </h1>
    <div class="person">
      <p class="person__name">Colin Matheny</p>
      <p class="person__title">Attorney</p>
    </div>
    <address class="address">118B Harbor Lane<br>Palm Cove, Florida 33412</address>
    <ul class="contacts">
      <li><svg viewBox="0 0 24 24"><path d="M6.6 10.8a15 15 0 0 0 6.6 6.6l2.2-2.2c.3-.3.7-.4 1-.2 1.1.4 2.3.6 3.6.6.6 0 1 .4 1 1V20c0 .6-.4 1-1 1A17 17 0 0 1 3 4c0-.6.4-1 1-1h3.5c.6 0 1 .4 1 1 0 1.3.2 2.5.6 3.6.1.3 0 .7-.2 1z"/></svg>555-014-2736</li>
      <li><svg viewBox="0 0 24 24"><path d="M7 2h10v6H7zM3 9h18v11H3zM6 13h4v4H6zm7 0h5v1h-5zm0 3h5v1h-5z"/></svg>555-018-4410</li>
      <li><svg viewBox="0 0 24 24"><path d="M2 5h20v14H2zm2 2v.5l8 5 8-5V7l-8 5z"/></svg>colin@mathenylaw.com</li>
      <li><svg viewBox="0 0 24 24"><circle cx="12" cy="12" r="10"/></svg>www.mathenylaw.com</li>
    </ul>
    <div class="accent-bar accent-bar--bottom"></div>
  </section>

  <section class="card card--back" aria-label="Business card back">
    <div class="back-mark">Law Offices of Colin Matheny</div>
    <ul class="practice-areas">
      <li>Civil Litigation</li>
      <li>Corporate Law</li>
      <li>Business Governance</li>
      <li>Real Estate Law</li>
    </ul>
  </section>
</main>
</body>
</html>
```